Need Website Design for Non-Profit Veteran Site

I am looking for a very talented creative website designer for a modern feel. I'll give a little bit of guidance around what I am looking for and then your creative juices should kick in and design away. I have already purchased the domain but will need hosting (at least temporarily) and the creative design work done.The website domain is militarydocs.orgI am looking to attract current and veteran military providers (doctors, nurse practitioners, physician assistants, etc) to join and signup for membership. They would pay a yearly fee to join. Would need membership categories $135 for Provider, $55 Student, $100 for Retired, and Organization (Organization would be broken down into Less than 100 ($200), 100-249 ($250), 250-499 ($300), 500-999 ($400), 1,000-2,999 ($500), and 3,000 ($700). Would need Benefit built out and would need to accept money through CoinVane and other means. Since it's a new organization just starting, would also need a Donate button to get people to donate if they want any amount they would like. The second part of the website is that once they join, they will have acess to a list of all other providers who have registered within the website (not exportable) so they can connect with one another. If they want to see contact information this will be included in their fee as a benefit to socialize with one another. As part of the website, there will be another Veteran's portal so veterans who would like to connect with a provider around a particular speciality can reach out and request help from the doctor writing a nexus letter or letter to support the veteran who is filing a claim with the BQ. Veterans would pay a yearly sign-up fee of $30.00 and would need their membership benefits displayed. They would have access to a list of veterans in their region by state and distance, and can reach out to doctors to get their help. If a doctor and veteran agree, sharable inforamtion of medical hipaa documents can be exchanged via the website. The physician and veteran can negotiate a fee through the website only and share their details. This is a separate fee for this type of process between the provider and veteran. We will collect a $250 fee for admin on each of these and each project the veteran does with the provider will cost $450 (so essentially the doctor gets paid $450 and i get $250.00. This model could be changed over time as we start to test this out). A good example of 50% of what I'm looking for is something like the following website: https://www.lpkt.org/ It has some of the features but not all and my site should be more modernized to attract the veteran and military providers.

Target Market(s)

Current and retired military providers and veterans

Industry/Entity Type

Non Profit

Number of Pages Required

1 page

Requirements
Must have
• Military Design
• Modern Feel (Example templates for feel -https://quillmoth.com/free-photoshop-psd-web-design-template/)
• Donation box
• Stuff mentioned in the description)
Nice to have
• Open to feedback
Should not have
• Open to feedback

```html
<!DOCTYPE html>
<html lang="en">
<head>
<meta charset="utf-8">
<title>Harborwell</title>
<link rel="stylesheet" href="https://fonts.googleapis.com/css2?family=Bebas+Neue&family=Open+Sans:wght@400;600;700&display=swap">
<style>
:root{
  --olive-dark:#45473a;
  --olive-deeper:#3a3c31;
  --olive-mid:#7f8562;
  --olive-light:#a9ad85;
  --emblem:#5a5d4a;
  --emblem-light:#6a6d58;
  --sand:#ddd49b;
  --sand-deep:#d2c98c;
  --disc:#4a4a44;
  --disc-dark:#2e2e2a;
  --ink:#2b2b28;
  --body:#4a4a45;
  --white:#ffffff;
}
*{margin:0;padding:0;box-sizing:border-box}
html,body{width:1200px;height:3158px;overflow:hidden;background:var(--white)}
body{font-family:"Open Sans",Arial,sans-serif;color:var(--body);position:relative}
.display{font-family:"Bebas Neue",Impact,sans-serif;font-weight:400;letter-spacing:.5px}
section,header,footer{position:absolute;left:0;width:1200px;overflow:hidden}

/* Navigation */
.site-nav{top:0;height:88px;background:var(--olive-dark);border-bottom:3px solid #d9d9cf}
.brand-tab{position:absolute;left:0;top:0;height:85px;width:360px;background:var(--olive-light);clip-path:polygon(0 0,100% 0,86% 100%,0 100%)}
.brand-name{position:absolute;left:99px;top:24px;font-size:38px;color:var(--white)}
.nav-links{position:absolute;right:96px;top:32px;display:flex;gap:33px;list-style:none}
.nav-links li{font-size:15px;font-weight:700;color:var(--white);text-transform:uppercase}

/* Hero */
.hero{top:88px;height:518px}
.hero-photo{position:absolute;inset:0;background:linear-gradient(100deg,#c9c6bf 0%,#b7b09f 35%,#8c8b72 55%,#cfc5b3 75%,#e6e4e1 100%)}
.hero-card{position:absolute;left:99px;top:106px;width:539px;height:307px;background:rgba(58,60,49,.82);padding:40px 24px}
.hero-title{font-size:80px;color:var(--white);line-height:1}
.hero-text{margin-top:14px;font-size:15px;font-weight:600;color:var(--white);line-height:1.55;width:440px}
.btn-skew{display:inline-block;font-family:"Bebas Neue",Impact,sans-serif;font-size:20px;color:var(--white);padding:10px 26px;clip-path:polygon(10% 0,100% 0,90% 100%,0 100%)}
.hero-btn{margin-top:24px;border:2px solid var(--white);clip-path:none;transform:skewX(-18deg);padding:8px 22px}
.hero-btn span{display:inline-block;transform:skewX(18deg)}
.hero-arrow{position:absolute;top:228px}

/* Donation */
.donation{top:606px;height:626px;background:var(--sand)}
.camo{position:absolute;inset:0}
.section-title{font-size:40px;color:var(--ink);text-align:center}
.donation .section-title{position:absolute;top:64px;width:100%}
.rule{position:absolute;height:2px;background:var(--ink);width:54px}
.donation .rule{left:573px;top:132px}
.disc{position:absolute;border-radius:50%;background:var(--disc);border:6px solid rgba(255,255,255,.35);box-shadow:0 0 0 3px rgba(120,116,80,.25);text-align:center;color:var(--white)}
.disc-icon{display:block;margin:0 auto}
.disc-title{font-family:"Bebas Neue",Impact,sans-serif}
.disc-text{font-size:10px;font-weight:600;line-height:1.35;margin:6px auto 0}
.disc.lg{background:var(--disc-dark)}
.donate-btn{position:absolute;left:540px;top:500px;background:var(--olive-dark)}

/* About */
.about{top:1232px;height:511px;background:var(--white)}
.about-photo{position:absolute;left:516px;top:0;width:684px;height:511px;background:linear-gradient(90deg,#ffffff 0%,#eef0f1 30%,#dfe3e6 60%,#eef1f2 100%)}
.about-body{position:absolute;left:99px;top:70px;width:514px}
.about h2{font-size:40px;color:var(--ink)}
.about .rule{position:static;margin:24px 0 30px;width:100px}
.about p{font-size:13px;line-height:1.65;margin-bottom:12px}
.about .btn-skew{margin-top:16px;background:var(--olive-dark)}

/* Membership */
.membership{top:1743px;height:514px;background:var(--olive-dark)}
.membership-field{position:absolute;inset:0;background:var(--olive-mid);clip-path:polygon(590px 0,1200px 0,1200px 514px,242px 514px)}
.membership-emblem{position:absolute;left:99px;top:78px;width:214px;height:220px;background:radial-gradient(circle at 50% 40%,var(--emblem-light) 0%,var(--emblem) 70%);border-radius:46% 46% 18% 18%}
.membership-body{position:absolute;right:99px;top:72px;width:640px;text-align:right;color:var(--white)}
.membership h2{font-size:40px}
.membership .rule{position:static;background:var(--white);width:90px;margin:14px 0 30px auto}
.membership p{font-size:15px;font-weight:600;line-height:1.75;margin-bottom:18px}
.member-actions{margin-top:34px;display:flex;justify-content:flex-end;gap:18px}
.member-actions span{font-family:"Bebas Neue",Impact,sans-serif;font-size:20px;width:104px;height:48px;line-height:48px;text-align:center;border:2px solid var(--white)}
.join{background:var(--white);color:var(--ink)}

/* Benefits */
.benefits{top:2257px;height:490px;background:var(--white)}
.benefits-photo{position:absolute;left:0;top:0;width:484px;height:490px;background:linear-gradient(90deg,#d8dedb 0%,#eaeeee 50%,#ffffff 100%)}
.benefits-body{position:absolute;left:520px;top:94px;width:585px}
.benefits h2{font-size:40px;color:var(--ink)}
.benefits .rule{position:static;width:90px;margin:14px 0 36px}
.benefit-list{list-style:none}
.benefit-list li{position:relative;padding-left:30px;font-size:13px;font-weight:600;color:var(--ink);line-height:1.75;margin-bottom:12px}
.benefit-list svg{position:absolute;left:0;top:5px}

/* Footer */
.site-footer{top:2747px;height:411px;background:var(--olive-dark);color:var(--white);text-align:center}
.footer-brand{position:absolute;top:90px;width:100%;font-size:40px}
.socials{position:absolute;top:172px;left:0;width:100%;display:flex;justify-content:center;gap:9px}
.socials span{width:44px;height:44px;border:2px solid var(--white);border-radius:50%;display:flex;align-items:center;justify-content:center}
.contacts{position:absolute;top:250px;width:100%;display:flex;justify-content:center;gap:48px;font-size:17px;font-weight:600}
.contacts div{display:flex;align-items:center;gap:14px}
.ring{width:40px;height:40px;border:2px solid var(--white);border-radius:50%;display:flex;align-items:center;justify-content:center}
.footer-rule{position:absolute;top:331px;left:400px;width:758px;height:1px;background:rgba(255,255,255,.45)}
.copyright{position:absolute;top:357px;width:100%;font-size:14px;font-weight:600}
</style>
</head>
<body>

<header class="site-nav">
  <div class="brand-tab"></div>
  <div class="brand-name display">HARBORWELL</div>
  <ul class="nav-links">
    <li>Home</li><li>Features</li><li>Book Now</li><li>Veteran</li><li>Prices</li><li>About</li><li>Contact Us</li>
  </ul>
</header>

<section class="hero">
  <div class="hero-photo" role="img" aria-label="Photo of a uniformed service member reading a letter during a consultation in a bright living room"></div>
  <div class="hero-card">
    <h1 class="hero-title display">HARBORWELL</h1>
    <p class="hero-text">Nemo enim ipsam voluptatem quia voluptas sit asperna tur aut odit aut fugit, sed quia.</p>
    <span class="btn-skew hero-btn"><span>Veterans Sign-Up</span></span>
  </div>
  <svg class="hero-arrow" style="left:38px" width="30" height="60" viewBox="0 0 30 60"><polyline points="26,2 4,30 26,58" fill="none" stroke="#fff" stroke-width="2"/></svg>
  <svg class="hero-arrow" style="right:38px" width="30" height="60" viewBox="0 0 30 60"><polyline points="4,2 26,30 4,58" fill="none" stroke="#fff" stroke-width="2"/></svg>
</section>

<section class="donation">
  <svg class="camo" width="1200" height="626" aria-hidden="true">
    <path d="M0 80 C120 40 220 140 340 90 S560 40 620 120 S860 200 980 110 S1150 60 1200 100 V0 H0Z" fill="var(--sand-deep)" opacity=".6"/>
    <path d="M0 470 C160 420 260 540 420 500 S700 420 820 520 S1080 560 1200 480 V626 H0Z" fill="var(--sand-deep)" opacity=".6"/>
  </svg>
  <h2 class="section-title display">Donation</h2>
  <div class="rule"></div>

  <div class="disc" style="left:95px;top:230px;width:190px;height:190px;padding-top:24px">
    <svg class="disc-icon" width="40" height="40" viewBox="0 0 40 40"><path d="M20 34 L6 20 A8 8 0 0 1 20 10 A8 8 0 0 1 34 20 Z" fill="#fff"/></svg>
    <div class="disc-title" style="font-size:18px;margin-top:10px">Nemo Enim Ipsam</div>
    <p class="disc-text" style="width:110px">Sed ut perspiciatis unde omnis iste natus error sit.</p>
  </div>
  <div class="disc" style="left:268px;top:210px;width:232px;height:232px;padding-top:30px">
    <svg class="disc-icon" width="48" height="48" viewBox="0 0 48 48"><circle cx="26" cy="16" r="11" fill="none" stroke="#fff" stroke-width="3"/><text x="26" y="21" text-anchor="middle" font-family="Open Sans" font-weight="700" font-size="14" fill="#fff">$</text><path d="M4 40 H14 L22 34 H34 L42 30" fill="none" stroke="#fff" stroke-width="3" stroke-linejoin="round"/></svg>
    <div class="disc-title" style="font-size:21px;margin-top:12px">Nemo Enim Ipsam</div>
    <p class="disc-text" style="width:130px">Sed ut perspiciatis unde omnis iste natus error sit.</p>
  </div>
  <div class="disc lg" style="left:474px;top:186px;width:252px;height:252px;padding-top:30px">
    <svg width="60" height="60" viewBox="0 0 60 60" style="display:block;margin:0 auto"><circle cx="30" cy="22" r="17" fill="#fff"/><text x="30" y="30" text-anchor="middle" font-family="Open Sans" font-weight="700" font-size="22" fill="#2e2e2a">$</text><path d="M6 46 Q30 58 54 44" stroke="#fff" stroke-width="4" fill="none"/></svg>
    <div class="disc-title" style="font-size:27px;margin-top:10px">Nemo Enim Ipsam</div>
    <p class="disc-text" style="width:160px;font-size:13px">Sed ut perspiciatis unde omnis iste natus error sit.</p>
  </div>
  <div class="disc" style="left:700px;top:210px;width:232px;height:232px;padding-top:30px">
    <svg class="disc-icon" width="48" height="48" viewBox="0 0 48 48"><rect x="8" y="20" width="32" height="22" fill="none" stroke="#fff" stroke-width="3"/><rect x="5" y="13" width="38" height="8" fill="#fff"/><path d="M24 13 V42" stroke="#fff" stroke-width="3"/><path d="M24 13 C18 4 10 8 16 13 M24 13 C30 4 38 8 32 13" fill="none" stroke="#fff" stroke-width="3"/></svg>
    <div class="disc-title" style="font-size:21px;margin-top:12px">Nemo Enim Ipsam</div>
    <p class="disc-text" style="width:130px">Sed ut perspiciatis unde omnis iste natus error sit.</p>
  </div>
  <div class="disc" style="left:915px;top:230px;width:190px;height:190px;padding-top:24px">
    <svg class="disc-icon" width="40" height="40" viewBox="0 0 40 40"><path d="M20 35 L5 20 A8.5 8.5 0 0 1 20 9 A8.5 8.5 0 0 1 35 20 Z" fill="none" stroke="#fff" stroke-width="3"/><text x="20" y="25" text-anchor="middle" font-family="Open Sans" font-weight="700" font-size="13" fill="#fff">$</text></svg>
    <div class="disc-title" style="font-size:18px;margin-top:10px">Nemo Enim Ipsam</div>
    <p class="disc-text" style="width:110px">Sed ut perspiciatis unde omnis iste natus error sit.</p>
  </div>

  <span class="btn-skew donate-btn">Donate</span>
</section>

<section class="about">
  <div class="about-photo" role="img" aria-label="Photo of a smiling doctor in a white coat with a stethoscope, arms crossed"></div>
  <div class="about-body">
    <h2 class="display">About Harborwell</h2>
    <div class="rule"></div>
    <p>Nemo enim ipsam voluptatem quia voluptas sit aspernatur aut odit aut fugit, sed quia consequuntur magni dolores eos qui ratione voluptatem sequi nesciunt. Neque porro quisquam est, qui dolorem ipsum quia dolor sit amet, consectetur, adipisci velit, sed quia non numquam eius modi tempora.</p>
    <p>Ut enim ad minima veniam, quis nostrum exercitationem ullam corporis suscipit laboriosam, nisi ut aliquid ex ea commodi consequatur? Quis autem vel eum iure reprehenderit qui in ea voluptate velit esse quam nihil molestiae consequatur, vel illum qui dolorem eum fugiat.</p>
    <span class="btn-skew">Read More</span>
  </div>
</section>

<section class="membership">
  <div class="membership-field"></div>
  <div class="membership-emblem" role="img" aria-label="Illustration of a sailor silhouette in uniform and cap"></div>
  <div class="membership-body">
    <h2 class="display">Our Membership</h2>
    <div class="rule"></div>
    <p>Nemo enim ipsam voluptatem quia voluptas sit aspernatur aut odit aut fugit, sed quia consequuntur magni dolores eos qui ratione voluptatem sequi nesciunt. Neque porro quisquam est, qui dolorem ipsum</p>
    <p>Neque porro quisquam est, qui dolorem ipsum quia dolor sit amet, consectetur, ad ipisci velit, sed quia non numquam eius modi tem pora.</p>
    <div class="member-actions"><span class="join">Join</span><span>Signup</span></div>
  </div>
</section>

<section class="benefits">
  <div class="benefits-photo" role="img" aria-label="Photo of a doctor writing notes on a tablet beside a window plant"></div>
  <div class="benefits-body">
    <h2 class="display">Our Benefits</h2>
    <div class="rule"></div>
    <ul class="benefit-list">
      <li><svg width="18" height="12" viewBox="0 0 18 12"><path d="M0 6H14M9 1L15 6L9 11" stroke="#2b2b28" stroke-width="2.4" fill="none"/></svg>Veterans would pay a yearly sign-up fee of $30.00 and would need their membership benefits displayed.</li>
      <li><svg width="18" height="12" viewBox="0 0 18 12"><path d="M0 6H14M9 1L15 6L9 11" stroke="#2b2b28" stroke-width="2.4" fill="none"/></svg>They would have access to a list of veterans in their region by state and distance, and can reach out to doctors to get their help.</li>
      <li><svg width="18" height="12" viewBox="0 0 18 12"><path d="M0 6H14M9 1L15 6L9 11" stroke="#2b2b28" stroke-width="2.4" fill="none"/></svg>If a doctor and veteran agree, sharable inforamtion of medical hipaa documents can be exchanged via the website.</li>
      <li><svg width="18" height="12" viewBox="0 0 18 12"><path d="M0 6H14M9 1L15 6L9 11" stroke="#2b2b28" stroke-width="2.4" fill="none"/></svg>The physician and veteran can negotiate a fee through the website only and share their details.</li>
    </ul>
  </div>
</section>

<footer class="site-footer">
  <svg class="camo" width="1200" height="411" aria-hidden="true">
    <path d="M0 60 C140 20 260 120 420 70 S700 20 820 90 S1060 140 1200 60 V0 H0Z" fill="var(--olive-deeper)" opacity=".7"/>
  </svg>
  <div class="footer-brand display">HARBORWELL</div>
  <div class="socials">
    <span aria-label="Website"><svg width="20" height="20" viewBox="0 0 20 20"><circle cx="10" cy="10" r="8" fill="none" stroke="#fff" stroke-width="1.8"/><ellipse cx="10" cy="10" rx="3.5" ry="8" fill="none" stroke="#fff" stroke-width="1.6"/><path d="M2 10H18" stroke="#fff" stroke-width="1.6"/></svg></span>
    <span aria-label="Chat"><svg width="20" height="20" viewBox="0 0 20 20"><path d="M3 4H17V13H8L4 17V13H3Z" fill="#fff"/></svg></span>
    <span aria-label="Share"><svg width="20" height="20" viewBox="0 0 20 20"><circle cx="15" cy="4" r="2.6" fill="#fff"/><circle cx="5" cy="10" r="2.6" fill="#fff"/><circle cx="15" cy="16" r="2.6" fill="#fff"/><path d="M15 4L5 10L15 16" fill="none" stroke="#fff" stroke-width="1.8"/></svg></span>
    <span aria-label="Alerts"><svg width="20" height="20" viewBox="0 0 20 20"><path d="M10 2C6.5 2 5 5 5 8V12L3 15H17L15 12V8C15 5 13.5 2 10 2Z" fill="#fff"/><circle cx="10" cy="17" r="1.8" fill="#fff"/></svg></span>
  </div>
  <div class="contacts">
    <div><span class="ring"><svg width="18" height="18" viewBox="0 0 24 24"><path d="M6 2l4 4-2 3c1 3 4 6 7 7l3-2 4 4-3 4C10 22 2 14 2 5z" fill="#fff"/></svg></span>+180 555 0142</div>
    <div><span class="ring"><svg width="18" height="14" viewBox="0 0 18 14"><rect x="1" y="1" width="16" height="12" fill="none" stroke="#fff" stroke-width="2"/><path d="M1 1l8 7 8-7" fill="none" stroke="#fff" stroke-width="2"/></svg></span>info@harborwellnet.org</div>
  </div>
  <div class="footer-rule"></div>
  <p class="copyright">Copyrights @ 2018 Harborwell. All Rights Reserved.</p>
</footer>

</body>
</html>
```